"Beyond The Grey Harbor" Fictional Book Cover

BEYOND THE GREY HARBOR
By: Derek Falloway

Here's the intro .

"It had been nearly forty years since Tim Ashworth last went to the island from where he was raised. Three months earlier he never would have thought about ever coming back. But life is weird. Things happen quickly and plans change, especially when your very life is at stake. The reason he was going back wasn’t to see old friends...no, no, no. They’re all dead. Of all the kids he grew up with on the island who moved off, he’s the only one still alive. Why?"

Pretty much all just a Lumora book, by the way.

Target Market(s)

fiction readers

Requirements
Must have
• Somewhat of a dark, mysterious cover is what I'd like to see. Use your imagination. I've never written a fiction book before so I'm very open to ideas

Needs to have my name, DEREK FALLOWAY at the bottom. like my other books, all of which are non-fiction
Nice to have
• Mysterious is what I'm looking for. NOT A HORROR story though. More a guy who left the island years ago, but is being called back to escape the rat race of modern, consumerist culture.

Please remember this NEEDS to jump out as a thumbnail on Brevix as people are browsing. Mainly the WORDS need to stick out. Lighter words on a say a blue background.

If you want to try to use the attached pic, or something like this, to reflect an island in the cover, that'd be good.

I've also uploaded a couple images I purchased from Pictoravault, hopefully you can make something work with these.

```html
<!DOCTYPE html>
<html lang="en">
<head>
<meta charset="utf-8">
<title>Beyond The Grey Harbor — Derek Falloway</title>
<link rel="stylesheet" href="https://fonts.googleapis.com/css2?family=Barlow:wght@300;500&family=Yellowtail&display=swap">
<style>
  :root {
    --sky-top: #2f2747;
    --sky-mid: #5a4468;
    --sky-glow: #c79a86;
    --sun: #fff1c8;
    --shore: #2a2230;
    --water: #231c30;
    --ink: #ffffff;
    --shadow: rgba(20, 12, 30, 0.85);
  }
  * { margin: 0; padding: 0; box-sizing: border-box; }
  html, body {
    width: 840px;
    height: 1200px;
    overflow: hidden;
    background: var(--water);
  }
  .cover {
    position: relative;
    width: 840px;
    height: 1200px;
    overflow: hidden;
  }
  .cover-photo {
    position: absolute;
    inset: 0;
    width: 840px;
    height: 1200px;
  }
  .title {
    position: absolute;
    left: 0;
    right: 0;
    text-align: center;
    color: var(--ink);
    font-family: "Barlow", sans-serif;
    font-weight: 500;
    text-shadow: 2px 3px 0 var(--shadow);
  }
  .title-line-top {
    top: 96px;
    font-size: 124px;
    line-height: 1;
    letter-spacing: 1px;
  }
  .title-connector {
    position: absolute;
    top: 240px;
    left: 0;
    right: 0;
    display: flex;
    align-items: center;
    justify-content: center;
    gap: 26px;
  }
  .connector-rule {
    width: 170px;
    height: 2px;
    background: var(--ink);
    box-shadow: 1px 2px 0 var(--shadow);
  }
  .connector-word {
    font-family: "Yellowtail", cursive;
    color: var(--ink);
    font-size: 84px;
    line-height: 1;
    text-shadow: 2px 3px 0 var(--shadow);
  }
  .title-line-bottom {
    top: 330px;
    font-size: 118px;
    line-height: 1;
    letter-spacing: 0;
  }
  .author {
    position: absolute;
    left: 0;
    right: 0;
    top: 1066px;
    text-align: center;
    color: var(--ink);
    font-family: "Barlow", sans-serif;
    font-weight: 300;
    font-size: 48px;
    letter-spacing: 11px;
  }
</style>
</head>
<body>
<main class="cover">
  <svg class="cover-photo" viewBox="0 0 840 1200" role="img" aria-label="Photograph of an island ferry pier at sunset, with trees and houses along the shore under a purple sky and dark water in front">
    <defs>
      <linearGradient id="sky" x1="0" y1="0" x2="0" y2="1">
        <stop offset="0" stop-color="var(--sky-top)"/>
        <stop offset="0.3" stop-color="var(--sky-mid)"/>
        <stop offset="0.52" stop-color="var(--sky-glow)"/>
        <stop offset="0.6" stop-color="#6a5060"/>
        <stop offset="0.8" stop-color="var(--shore)"/>
        <stop offset="1" stop-color="var(--water)"/>
      </linearGradient>
      <radialGradient id="sun" cx="70" cy="620" r="320" gradientUnits="userSpaceOnUse">
        <stop offset="0" stop-color="var(--sun)" stop-opacity="1"/>
        <stop offset="0.25" stop-color="#f0c08a" stop-opacity="0.7"/>
        <stop offset="1" stop-color="#c79a86" stop-opacity="0"/>
      </radialGradient>
    </defs>
    <rect width="840" height="1200" fill="url(#sky)"/>
    <rect width="840" height="1200" fill="url(#sun)"/>
  </svg>

  <h1 class="title title-line-top">Beyond</h1>
  <div class="title-connector">
    <span class="connector-rule"></span>
    <span class="connector-word">the</span>
    <span class="connector-rule"></span>
  </div>
  <p class="title title-line-bottom">Grey Harbor</p>

  <p class="author">DEREK FALLOWAY</p>
</main>
</body>
</html>
```